Residential Mortgage Leader needs Wordpress Design

Looking for a home page website design for a client. We develop using the WordPress platform and would prefer the design be at least loosely based on an existing WordPress template. Attached files have many notes from our creative brief with client. The site must be responsive. Approved, basic wireframe attached. There is room for interpretation.

Existing web site: http://www.marisolkettering.example/

The Marisol Kettering Team relies on strong systems to deliver an on-time, done-right, friendly experience. Marisol offers mortgages and refinancing services throughout the United States. She is a successful Brookvale Funding agent who strives to be an active part of her community. She would like to focus the site on her team, rather than just her.

Difference makers...
When you work with the Marisol Kettering team you get a high level of expertise and a friendly experience.

She has amazing credentials. Marisol is widely recognized as a top producer for her company, and has earned a number of awards and honors for her customer service.

Marisol's team is very engaged and enjoys sharing social comments or photos from their community.

Imagery:
* Friendly, warm imagery, preferably of her team or an image to represent her team
* Clean and crisp
* Professional / Experts in mortgage and refinance
* Clean / Good use of white space
Updates

When possible, please use imagery from the DFW area. The client mentioned they would prefer not to see stock images. Thanks.

Amend that- creative use of stock images, however, is fine. A few designs have used stock imagery, but in a well-considered manner.

We added some photos and graphics that are local. We are Dallas / Ft. Worth, Plano, Frisco, Texas. We also added some examples of photos to use for the "In the Community" area. Stock photos of business folks just doesn't fit there. Thanks!

Target Market(s)

They service a lot of builders, but also work with homeowners. Their typical client is usually a woman searching for mortgage services online. She typically has a family and may refer her husband to Marisol's team. Keep in mind, however, they also see a number of other scenarios. Most of their clients are middle to high-end borrowers.

Industry/Entity Type

It Company

Requirements
Must have
• Design should be developed using program such as Photoshop or Fireworks or Illustrator as last preference. Ideally, the design would be based on an existing responsive WordPress theme, which we would customize. You must include the name of the target theme. The footer should include lots of space for disclaimers and legal language. Site navigation should include these choices: "Home, About, Builders, Mortgage Info, Approval, Blog, Contact"
Nice to have
• Blog, social media and photos area. Use of the already approved style prototype with colors and fonts (Lato- a Google font, Times New Roman and Cookie-a decorative Google font). However, we are open to interpretation.
Should not have
• Hard to read fonts or a lack of white space.

```html
<!DOCTYPE html>
<html lang="en">
<head>
<meta charset="utf-8">
<title>Brookvale Funding – Marisol Kettering Team</title>
<link href="https://fonts.googleapis.com/css2?family=Lato:wght@300;400;700&display=swap" rel="stylesheet">
<style>
:root{
  --red:#c0281d;
  --dark:#2b2b2b;
  --darker:#252525;
  --hero:#444;
  --light:#f1f1f1;
  --text-light:#cfcfcf;
  --text-muted:#a9a9a9;
  --text-dark:#3a3a3a;
  --rule:#d6d6d6;
  --white:#fff;
}
*{margin:0;padding:0;box-sizing:border-box}
html,body{width:895px;height:1200px;overflow:hidden}
body{position:relative;font-family:'Lato',sans-serif;background:var(--light);color:var(--text-dark)}
.abs{position:absolute}
.top-stripe{left:0;top:0;width:895px;height:4px;background:repeating-linear-gradient(90deg,#c0281d 0 30px,#555 30px 46px,#d9d4c4 46px 76px,#555 76px 92px)}
.header{left:0;top:4px;width:895px;height:60px;background:var(--dark);border-bottom:1px dashed #444}
.brand{left:89px;top:25px;color:var(--white)}
.brand-name{font-size:19px;font-weight:700;color:var(--white);display:flex;align-items:center;gap:6px}
.brand-name .mark{width:12px;height:12px;background:var(--red)}
.brand-sub{font-size:8px;font-weight:700;margin-top:2px}
.nav{left:335px;top:23px;display:flex;gap:0}
.nav a{display:block;font-size:10px;font-weight:700;color:var(--white);text-decoration:none;height:24px;line-height:24px;padding:0 10px;margin-right:16px}
.nav a.active{background:var(--red);border-radius:2px}
.hero{left:0;top:64px;width:895px;height:298px;background:var(--hero)}
.slide{left:110px;top:87px;width:674px;height:225px;background:linear-gradient(90deg,#9fcf5a 0%,#5aa52a 45%,#4a9a22 70%,#7fc24a 100%)}
.slide-copy{left:402px;top:122px;width:300px;color:var(--white)}
.slide-copy h1{font-size:29px;font-weight:700;line-height:34px}
.slide-copy p{font-size:11.5px;font-weight:700;line-height:17.5px;margin-top:10px}
.btn{display:inline-block;margin-top:17px;background:var(--red);color:var(--white);font-size:13px;padding:5px 16px;border-radius:2px}
.arrow{top:196px}
.dots{left:430px;top:322px;display:flex;gap:5px;align-items:center}
.dots span{width:7px;height:7px;border-radius:50%;background:#777}
.dots span.on{width:10px;height:10px;background:var(--white);border:2px solid #555}
.cred{left:0;top:362px;width:895px;height:173px;background:var(--dark);border-top:1px dashed #555;border-bottom:1px dashed #555}
.col-rule{top:374px;height:152px;border-left:1px dashed #4a4a4a}
.cred-col{top:397px;color:var(--text-light)}
.cred-col h2{font-size:16px;font-weight:400;color:var(--white);height:20px;display:flex;align-items:center;gap:10px}
.cred-col h3{font-size:11.5px;font-weight:400;color:var(--white);margin-top:10px}
.cred-col p{font-size:8.5px;line-height:16.8px;margin-top:9px;color:var(--text-muted)}
.sec-title{top:568px;font-size:16px;color:var(--red);padding-bottom:7px;border-bottom:1px solid var(--rule)}
.thumb{width:55px;height:43px}
.social-item{left:89px;display:flex;gap:10px;font-size:8.5px;line-height:16.5px;color:var(--text-dark)}
.social-item p{width:130px;padding-top:4px}
.blog-card{left:345px;width:209px;height:120px;background:var(--white);padding:4px;box-shadow:0 4px 6px rgba(0,0,0,.25)}
.blog-card div{width:100%;height:100%}
.caption{left:348px;font-size:8.5px;font-weight:700;color:#333}
.caption small{display:block;font-size:6.5px;font-weight:400;letter-spacing:1px;color:#888;margin-top:2px}
.comm-img{left:620px;width:189px;height:60px}
.comm-text{left:620px;width:190px;font-size:8.5px;line-height:16.8px}
.footer{left:0;top:965px;width:895px;height:185px;background:var(--dark)}
.f-brand{left:89px;top:990px;color:#ddd}
.f-brand .brand-name{font-size:15px;color:#ddd}
.f-brand .brand-sub{font-size:6.5px}
.f-about{left:88px;top:1030px;width:240px;font-size:8.5px;line-height:20px;color:var(--text-muted)}
.quick{left:372px;top:983px;color:var(--white)}
.quick h4{font-size:13px;font-weight:400;margin-bottom:6px}
.quick a{display:block;font-size:8.5px;line-height:19.8px;color:var(--text-muted);text-decoration:none}
.portrait{left:537px;top:977px;width:136px;height:159px;background:linear-gradient(180deg,#3a3230,#6b5648 55%,#2a2624)}
.contact{left:688px;top:976px;color:var(--text-muted)}
.contact h4{font-size:13px;font-weight:400;color:var(--white);line-height:18px;margin-bottom:8px}
.contact p{font-size:8.5px;line-height:19.8px}
.bottom{left:0;top:1150px;width:895px;height:50px;background:var(--light)}
.b-logo{left:88px;top:1171px;font-size:16px;color:var(--red);font-family:'Lato',sans-serif;font-weight:400}
.b-copy{left:201px;top:1180px;font-size:7.5px;color:#333}
.b-icon{top:1173px;width:17px;height:17px;border-radius:50%;background:#888}
</style>
</head>
<body>
<div class="abs top-stripe"></div>
<header class="abs header"></header>
<div class="abs brand">
  <div class="brand-name">Brookvale Funding <span class="mark"></span></div>
  <div class="brand-sub">A Harborline Capital Company</div>
</div>
<nav class="abs nav">
  <a class="active">Home</a><a>About</a><a>Builders</a><a>Mortage Info</a><a>Approval Blog</a><a>Contact Info</a>
</nav>

<section class="abs hero"></section>
<div class="abs slide" role="img" aria-label="Hand holding a paper house cut-out against bright green grass"></div>
<div class="abs slide-copy">
  <h1>Earning Your Business</h1>
  <p>Lorem Ipsum is simply dummy text of the printing and typesetting industry Lorem Ipsum has been the indust ry's standard dummy.</p>
  <span class="btn">Start Here</span>
</div>
<svg class="abs arrow" style="left:82px" width="12" height="22" viewBox="0 0 12 22"><path d="M10 2 2 11l8 9" fill="none" stroke="#333" stroke-width="3"/></svg>
<svg class="abs arrow" style="left:800px" width="12" height="22" viewBox="0 0 12 22"><path d="M2 2l8 9-8 9" fill="none" stroke="#333" stroke-width="3"/></svg>
<div class="abs dots"><span></span><span></span><span class="on"></span></div>

<section class="abs cred"></section>
<div class="abs col-rule" style="left:412px"></div>
<div class="abs col-rule" style="left:617px"></div>
<div class="abs cred-col" style="left:90px;width:290px">
  <h2 style="font-size:16px">Our Credentials</h2>
  <h3>A top-producer, top-notch</h3>
  <p>Lorem Ipsum is simply dummy text of the printing and typesetting industry. Lorem Ipsum has been the industry's standard dummy text ever since the 1500s, when an unknown printer took a galley of type and scrambled it to make a type specimen book.</p>
</div>
<div class="abs cred-col" style="left:426px;width:180px">
  <h2 style="font-size:13px"><svg width="14" height="18" viewBox="0 0 14 18"><rect x="1" y="1" width="12" height="14" fill="none" stroke="#bbb" stroke-width="1.2"/><circle cx="7" cy="10" r="2.5" fill="none" stroke="#bbb"/><path d="M5 13v4l2-1 2 1v-4" fill="none" stroke="#bbb"/></svg> Awards</h2>
  <h3>Lorem Ipsum is simply dummy text.</h3>
  <p>Lorem Ipsum is simply dummy text of the printing and typesetting industry. Lorem Ipsum has been the industry's standard dummy text ever since the 1500s.</p>
</div>
<div class="abs cred-col" style="left:632px;width:185px">
  <h2 style="font-size:13px"><svg width="14" height="18" viewBox="0 0 14 18"><ellipse cx="7" cy="9" rx="6" ry="8" fill="none" stroke="#bbb" stroke-width="1.2"/><ellipse cx="7" cy="9" rx="3" ry="5" fill="none" stroke="#bbb"/></svg> Recognion</h2>
  <h3>Lorem Ipsum is simply dummy text.</h3>
  <p>Lorem Ipsum is simply dummy text of the printing and typesetting industry. Lorem Ipsum has been the industry's standard dummy text ever since the 1500s.</p>
</div>

<h2 class="abs sec-title" style="left:90px;width:187px;font-weight:400">Social</h2>
<h2 class="abs sec-title" style="left:345px;width:209px;font-weight:400">Blog</h2>
<h2 class="abs sec-title" style="left:620px;width:189px;font-weight:400">In the Community</h2>

<div class="abs social-item" style="top:611px"><div class="thumb" role="img" aria-label="Hands exchanging house keys" style="background:linear-gradient(135deg,#5e7d9a,#8a7a5a)"></div><p>Lorem Ipsum is simply dummy text of the printing and</p></div>
<div class="abs social-item" style="top:672px"><div class="thumb" role="img" aria-label="Raised hands with social icons" style="background:linear-gradient(135deg,#e6e0dc,#c98a74)"></div><p>Lorem Ipsum is simply dummy text of the printing and</p></div>
<div class="abs social-item" style="top:735px"><div class="thumb" role="img" aria-label="Globe of connected profile photos" style="background:linear-gradient(135deg,#b9d4e4,#5d88a8)"></div><p>Lorem Ipsum is simply dummy text of the printing and</p></div>
<div class="abs social-item" style="top:799px"><div class="thumb" role="img" aria-label="Hand touching a network of people" style="background:linear-gradient(135deg,#1c2430,#8a5a30)"></div><p>Lorem Ipsum is simply dummy text of the printing and</p></div>
<div class="abs social-item" style="top:863px"><div class="thumb" role="img" aria-label="Glowing globe on dark background" style="background:radial-gradient(circle,#9ab8d0,#1b2a3a 70%)"></div><p>Lorem Ipsum is simply dummy text of the printing and</p></div>

<div class="abs blog-card" style="top:608px"><div role="img" aria-label="Traffic lights and tall building against blue sky" style="background:linear-gradient(160deg,#3d7fc9,#a9cbe8 55%,#6d7a5a)"></div></div>
<div class="abs caption" style="top:741px">Portfolio 1<small>BUILDINGS</small></div>
<div class="abs blog-card" style="top:778px"><div role="img" aria-label="Palm trees against a teal sky" style="background:linear-gradient(180deg,#4fa6b0,#c8e6e0)"></div></div>
<div class="abs caption" style="top:911px">Portfolio 2<small>NATURE</small></div>

<div class="abs comm-img" style="top:610px" role="img" aria-label="Group of friends jumping with arms raised" aria-roledescription="image" ><div style="width:100%;height:100%;background:linear-gradient(180deg,#3f7fd4,#7fb0ea 60%,#b9a08a)"></div></div>
<p class="abs comm-text" style="top:681px">Lorem Ipsum is simply dummy text of the and typesetting industry. Lorem Ipsum has been the industry's standard dummy text ever since the. 1500s when an unknown printer took.</p>
<div class="abs comm-img" style="top:779px" role="img" aria-label="Cupped hands holding soil with a seedling"><div style="width:100%;height:100%;background:linear-gradient(90deg,#b0704e,#5a3a24 50%,#7ea2c8)"></div></div>
<p class="abs comm-text" style="top:851px">Lorem Ipsum is simply dummy text of the and typesetting industry. Lorem Ipsum has been the industry's standard dummy text ever since the. 1500s when an unknown printer took.</p>

<footer class="abs footer"></footer>
<div class="abs f-brand">
  <div class="brand-name">Brookvale Funding <span class="mark" style="background:#ddd;width:10px;height:10px"></span></div>
  <div class="brand-sub">A Harborline Capital Company.</div>
</div>
<p class="abs f-about">Lorem Ipsum is simply dummy text of the printing and typesetting industry. Lorem Ipsum has been the industr y's standard dummy text ever since the 1500s, when an unknown printer took a galley of type and scrambled it to make a type specimen book.</p>
<div class="abs quick">
  <h4>Quick Link</h4>
  <a>Home</a><a>About</a><a>Builders</a><a>Mortagage Info</a><a>Approval Blogs</a><a>Contact us</a>
</div>
<div class="abs portrait" role="img" aria-label="Portrait of the branch manager"></div>
<div class="abs contact">
  <h4>Marisol Kettering,<br>Branch Manager</h4>
  <p>Office: 555.210.4400</p>
  <p>Cell: 555.318.6620</p>
  <p>mkettering@brookvalefunding.example</p>
  <p>NMLS: 10428</p>
  <p>2418 Linden Row , Ste. 140</p>
  <p>Maplewood, TX 75099</p>
</div>

<section class="abs bottom"></section>
<div class="abs b-logo">marisolkettering</div>
<div class="abs b-copy">Copyright © Brookvale Funding. All Rights Reserved.</div>
<div class="abs b-icon" style="left:717px"></div>
<div class="abs b-icon" style="left:743px"></div>
<div class="abs b-icon" style="left:769px"></div>
</body>
</html>
```